Business Card Brantley Digital

Design of two business cards (board) for Brantley Digital. Brantley Digital DMCC, based in in Dubai U.A.E. Brantley Digital is a self-contained online company, taking an online concept from idea to reality. Concretely, this has involved the (partly remote) management, website development, market implementation and mobile application development for several platforms.

Frontside of business card should feature our company logo (Brantley) and personal details. Backside should feature the logo's of our current brands (mendupnow, getsetdone and gatherguide). We would prefer a design based on the grey/orange color scheme of our company. Brantley Digital is a young, modern and dynamic company and we would like to see this reflected in the design.

Industry/Entity Type

Business

```html
<!DOCTYPE html>
<html lang="en">
<head>
<meta charset="utf-8">
<title>Brantley Digital – Business Cards</title>
<link href="https://fonts.googleapis.com/css2?family=Saira:wght@300;400;600&display=swap" rel="stylesheet">
<style>
  :root {
    --backdrop: #3b322b;
    --card-grey: #5b5b5d;
    --band-grey: #58585a;
    --orange: #f15a2b;
    --edge-red: #d8322a;
    --paper: #ffffff;
    --ink: #3c3c3e;
    --mark-light: #e4e4e4;
  }
  * { margin: 0; padding: 0; box-sizing: border-box; }
  html, body {
    width: 1200px; height: 901px; overflow: hidden;
    background: var(--backdrop);
    font-family: "Saira", sans-serif;
  }
  .board { position: relative; width: 1200px; height: 901px; }
  .card {
    position: absolute; top: 295px;
    width: 540px; height: 310px;
    box-shadow: 0 10px 24px rgba(0,0,0,0.45);
  }
  .card--back { left: 45px; }
  .card--front { left: 615px; }
  .card svg { display: block; width: 540px; height: 310px; }
  .brand-name { font-family: "Saira", sans-serif; font-weight: 300; fill: var(--orange); letter-spacing: 5px; }
  .person-name { font-weight: 600; font-size: 15px; fill: var(--orange); letter-spacing: 0.5px; }
  .person-role { font-weight: 400; font-size: 9px; fill: var(--ink); letter-spacing: 0.5px; }
  .contact-line { font-weight: 400; font-size: 11.5px; fill: var(--ink); }
</style>
</head>
<body>
<main class="board">

  <!-- Back side -->
  <section class="card card--back" aria-label="Business card back">
    <svg viewBox="0 0 540 310" xmlns="http://www.w3.org/2000/svg">
      <rect class="card-base" width="540" height="310" fill="var(--card-grey)"/>
      <polygon class="ribbon-left" points="0,118 0,150 112,40 158,40 146,26 158,12 104,12" fill="var(--orange)"/>
      <polygon class="ribbon-right" points="392,0 428,0 540,108 540,142" fill="var(--orange)"/>
      <rect class="edge-stripe" x="0" y="302" width="540" height="8" fill="var(--edge-red)"/>
      <circle class="brand-dot" cx="270" cy="118" r="40" fill="var(--mark-light)"/>
      <text class="brand-name" x="270" y="205" font-size="22" text-anchor="middle">BRANTLEY</text>
    </svg>
  </section>

  <!-- Front side -->
  <section class="card card--front" aria-label="Business card front">
    <svg viewBox="0 0 540 310" xmlns="http://www.w3.org/2000/svg">
      <rect class="card-base" width="540" height="310" fill="var(--paper)"/>
      <polygon class="band-top" points="352,0 540,0 540,50 408,22 342,40 366,10" fill="var(--band-grey)"/>
      <polygon class="band-diagonal" points="0,140 0,196 196,0 140,0" fill="var(--band-grey)"/>
      <rect class="edge-stripe" x="0" y="302" width="540" height="8" fill="var(--orange)"/>

      <g class="brand">
        <circle class="brand-dot" cx="405" cy="112" r="28" fill="var(--band-grey)"/>
        <text class="brand-name" x="405" y="170" font-size="20" text-anchor="middle">BRANTLEY</text>
      </g>

      <g class="online-links">
        <rect x="340" y="190" width="17" height="17" fill="var(--orange)"/>
        <circle cx="348.5" cy="198.5" r="4.5" fill="none" stroke="#fff" stroke-width="1.4"/>
        <text class="contact-line" x="366" y="202.5">www.brantleydigital.com</text>
        <rect x="340" y="216" width="17" height="17" fill="var(--orange)"/>
        <rect x="345" y="221" width="7" height="7" fill="#fff"/>
        <text class="contact-line" x="366" y="228.5">www.chirpline.net</text>
        <rect x="340" y="242" width="17" height="17" fill="var(--orange)"/>
        <rect x="345" y="247" width="7" height="7" fill="#fff"/>
        <text class="contact-line" x="366" y="254.5">www.friendspace.net</text>
      </g>

      <g class="person">
        <text class="person-name" x="28" y="205">DANIEL REEVE</text>
        <text class="person-role" x="28" y="218">FINANCIAL ADVISOR</text>
      </g>

      <g class="contact">
        <rect x="28" y="228" width="17" height="17" fill="var(--orange)"/>
        <path d="M36.5 232 a3.6 3.6 0 0 1 3.6 3.6 c0 2.6 -3.6 6.4 -3.6 6.4 s-3.6 -3.8 -3.6 -6.4 a3.6 3.6 0 0 1 3.6 -3.6 z" fill="#fff"/>
        <circle cx="36.5" cy="235.6" r="1.3" fill="var(--orange)"/>
        <text class="contact-line" x="54" y="240.5">14 Harbor Lane</text>

        <rect x="28" y="253" width="17" height="17" fill="var(--orange)"/>
        <path d="M33 257 l2.6 0 l1 3 l-1.5 1.2 a7 7 0 0 0 3.2 3.2 l1.2 -1.5 l3 1 l0 2.6 a1.3 1.3 0 0 1 -1.4 1.2 a10 10 0 0 1 -9.2 -9.2 a1.3 1.3 0 0 1 1.1 -1.5 z" fill="#fff"/>
        <text class="contact-line" x="54" y="265.5">045 550 1927</text>

        <rect x="28" y="278" width="17" height="17" fill="var(--orange)"/>
        <rect x="32" y="282.5" width="9" height="7" fill="none" stroke="#fff" stroke-width="1.2"/>
        <polyline points="32,282.5 36.5,286.5 41,282.5" fill="none" stroke="#fff" stroke-width="1.2"/>
        <text class="contact-line" x="54" y="290.5">dreeve@mailbox.net</text>
      </g>
    </svg>
  </section>

</main>
</body>
</html>
```